Business Cards - Brightpath Horizon

need to design unique business card for my mortgage business. I need to design credit card style business card for my business or any unique idea that you might have

Target Market(s)

Home Loan customers

Industry/Entity Type

Mortgage Brokerage

Contact Information for Business Card

please design credit card style or very unique style business card

Colors

Designer to choose colors to be used in the design.

Requirements
Must have
• Name
• position
• Phone number
• fax number
• email address
• website address
• social media address
• All above fields will be provided once design in finalised

```html
<!DOCTYPE html>
<html lang="en">
<head>
<meta charset="utf-8">
<title>Brightpath Horizon – Business Card</title>
<link rel="stylesheet" href="https://fonts.googleapis.com/css2?family=Roboto:wght@400;700&family=Roboto+Condensed:wght@700&display=swap">
<style>
  :root {
    --page-bg: #d9d6d2;
    --card-white: #f4f4f4;
    --brand-blue: #1c3fc4;
    --brand-orange: #f08a1c;
    --navy-deep: #03106a;
    --navy-mid: #0a2fc0;
    --wave-blue: #1a4be0;
    --wave-bronze: #8a6a3a;
    --gold: #f3d47a;
    --text-white: #ffffff;
  }
  * { box-sizing: border-box; margin: 0; padding: 0; }
  html, body { width: 1200px; height: 886px; overflow: hidden; }
  body {
    background: var(--page-bg);
    font-family: "Roboto", Arial, sans-serif;
    position: relative;
  }
  .card {
    position: absolute;
    top: 288px;
    width: 540px;
    height: 310px;
    border-radius: 22px;
    overflow: hidden;
    box-shadow: 0 10px 24px rgba(0,0,0,0.25);
  }

  /* Front */
  .card-front { left: 40px; background: var(--card-white); }
  .front-brand {
    position: absolute; left: 0; right: 0; top: 108px;
    text-align: center;
  }
  .brand-name {
    font-family: "Roboto", Arial, sans-serif;
    font-weight: 700;
    color: var(--brand-blue);
    font-size: 40px;
    line-height: 1.1;
    display: inline-flex; align-items: center; gap: 12px;
    white-space: nowrap;
  }
  .brand-dot {
    width: 18px; height: 18px; border-radius: 50%;
    background: var(--brand-orange); display: inline-block; flex: none;
  }
  .front-rule {
    position: absolute; left: 70px; right: 70px; top: 228px;
    display: flex; align-items: center; gap: 12px;
  }
  .front-rule .line { flex: 1; height: 1px; background: var(--brand-blue); opacity: 0.7; }
  .social-dot { width: 24px; height: 24px; border-radius: 50%; background: var(--brand-blue); }

  /* Back */
  .card-back {
    left: 620px;
    background: radial-gradient(ellipse at 45% 60%, var(--navy-mid) 0%, var(--navy-deep) 80%);
  }
  .card-back svg.wave { position: absolute; inset: 0; }
  .back-brand { position: absolute; right: 28px; top: 36px; }
  .back-brand .brand-name { color: var(--text-white); font-size: 26px; gap: 8px; }
  .back-brand .brand-dot { width: 12px; height: 12px; }
  .contact-list {
    position: absolute; left: 26px; top: 38px;
    list-style: none; color: var(--text-white); font-size: 13px;
  }
  .contact-list li { display: flex; align-items: center; gap: 8px; margin-bottom: 5px; }
  .contact-list svg { width: 13px; height: 13px; fill: var(--gold); }
  .card-number {
    position: absolute; left: 60px; top: 150px;
    font-family: "Roboto Condensed", Arial, sans-serif; font-weight: 700;
    font-size: 30px; letter-spacing: 14px; color: var(--gold);
    text-shadow: 0 1px 0 rgba(0,0,0,0.5);
  }
  .holder {
    position: absolute; left: 40px; bottom: 34px;
    font-family: "Roboto Condensed", Arial, sans-serif; color: var(--gold);
  }
  .holder .name { font-size: 20px; font-weight: 700; }
  .holder .role { font-size: 13px; font-weight: 700; letter-spacing: 0.5px; }
  .address {
    position: absolute; right: 28px; top: 200px; text-align: right;
    color: var(--text-white); font-size: 13px; line-height: 1.4;
  }
</style>
</head>
<body>

  <section class="card card-front">
    <div class="front-brand">
      <div class="brand-name"><span class="brand-dot"></span>Brightpath Horizon</div>
    </div>
    <div class="front-rule">
      <span class="line"></span>
      <span class="social-dot"></span>
      <span class="social-dot"></span>
      <span class="social-dot"></span>
      <span class="social-dot"></span>
      <span class="line"></span>
    </div>
  </section>

  <section class="card card-back">
    <svg class="wave" viewBox="0 0 540 310" preserveAspectRatio="none" aria-hidden="true">
      <path d="M250 0 C330 40 300 120 330 200 C350 260 400 290 420 310 L540 310 L540 0 Z" fill="var(--wave-blue)"/>
      <path d="M232 0 C310 40 282 120 312 200 C332 260 385 292 404 310 L420 310 C400 290 350 260 330 200 C300 120 330 40 250 0 Z" fill="var(--wave-bronze)" opacity="0.85"/>
    </svg>

    <ul class="contact-list">
      <li><svg viewBox="0 0 16 16"><path d="M3 1h3l1.5 4-2 1.5a9 9 0 0 0 4 4L11 8.5l4 1.5v3a2 2 0 0 1-2 2A12 12 0 0 1 1 3a2 2 0 0 1 2-2z"/></svg>415 730 2286</li>
      <li><svg viewBox="0 0 16 16"><path d="M1 3h14v10H1z M1 3l7 6 7-6" stroke="#03106a" stroke-width="1"/></svg>hello@brightpath.com</li>
      <li><svg viewBox="0 0 16 16"><circle cx="8" cy="8" r="7"/></svg>www.brightpath.com</li>
    </ul>

    <div class="back-brand">
      <div class="brand-name"><span class="brand-dot"></span>Brightpath Horizon</div>
    </div>

    <div class="card-number">514 826 3907</div>

    <div class="address">2140 Maple Ridge Road<br>Juneau, Alaska 99801</div>

    <div class="holder">
      <div class="name">DANIEL REYES</div>
      <div class="role">CEO/FOUNDER</div>
    </div>
  </section>

</body>
</html>
```